Floor Inspections and Consulting

We provide inspections and consulting services on various floor coverings, e.g. carpet, hardwood, etc. We also do expert witness work for attorneys due to floor covering failures. We current have a logo, just need it incorporated into a new design. I have examples of cards I have found on the internet that capture my attention and make a statement. I have included our original business card, which in my opinion is terrible, but it does have our logo on it.

```html
<!DOCTYPE html>
<html lang="en">
<head>
<meta charset="utf-8">
<title>Keystone Floor Reviews – Business Card</title>
<link rel="stylesheet" href="https://fonts.googleapis.com/css2?family=Montserrat:wght@600;700;800&family=Arimo:wght@400&display=swap">
<style>
  :root {
    --backdrop: #2e2e30;
    --card-orange: #f57c0e;
    --card-orange-deep: #e56f08;
    --card-sheen: rgba(255, 255, 255, 0.07);
    --ink-white: #ffffff;
    --rule-white: rgba(255, 255, 255, 0.55);
  }
  * { box-sizing: border-box; margin: 0; padding: 0; }
  html, body {
    width: 1200px; height: 1015px; overflow: hidden;
    background: var(--backdrop);
  }
  .canvas {
    position: relative; width: 1200px; height: 1015px;
    display: flex; flex-direction: column; align-items: center; justify-content: center; gap: 60px;
  }
  .card {
    position: relative; width: 640px; height: 366px; border-radius: 26px;
    background: linear-gradient(160deg, var(--card-orange-deep) 0%, var(--card-orange) 40%, var(--card-orange) 100%);
    overflow: hidden; color: var(--ink-white);
    box-shadow: 0 18px 40px rgba(0,0,0,0.45);
  }
  .card__sheen {
    position: absolute; left: 70px; top: 40px; width: 640px; height: 300px;
    border-radius: 50%; background: var(--card-sheen);
  }
  .brand {
    position: absolute; display: flex; flex-direction: column; align-items: center;
    font-family: "Montserrat", sans-serif;
  }
  .brand__mark {
    width: 64px; height: 64px; border: 5px solid var(--ink-white); border-radius: 50%;
    margin-bottom: 10px;
  }
  .brand__rule { width: 100%; height: 2px; background: var(--ink-white); }
  .brand__name {
    font-weight: 700; font-size: 27px; letter-spacing: 1.5px; line-height: 1.1;
    text-align: center; padding: 6px 0 4px; text-transform: uppercase;
  }
  .brand__sub {
    font-weight: 700; font-size: 10px; letter-spacing: 2.5px; text-transform: uppercase;
    padding-bottom: 6px;
  }
  .card--front .brand { left: 50%; top: 52px; transform: translateX(-50%); width: 430px; }
  .tagline {
    position: absolute; left: 0; right: 0; top: 250px; text-align: center;
    font-family: "Montserrat", sans-serif; font-weight: 700; font-size: 25px; line-height: 1.25;
  }
  .card--back .brand { left: 140px; top: 40px; width: 400px; }
  .holder {
    position: absolute; left: 48px; bottom: 50px;
    font-family: "Montserrat", sans-serif; font-weight: 700; font-size: 26px; letter-spacing: 1px;
    text-transform: uppercase;
  }
  .divider {
    position: absolute; left: 340px; top: 222px; width: 1px; height: 96px; background: var(--rule-white);
  }
  .contacts {
    position: absolute; left: 360px; top: 222px; list-style: none;
    font-family: "Arimo", sans-serif; font-size: 15px;
    display: flex; flex-direction: column; gap: 12px;
  }
  .contacts li { display: flex; align-items: center; gap: 9px; white-space: nowrap; }
  .contacts svg { width: 18px; height: 18px; flex: none; }
</style>
</head>
<body>
<main class="canvas">

  <section class="card card--front" aria-label="Card front">
    <div class="card__sheen"></div>
    <div class="brand">
      <div class="brand__mark"></div>
      <div class="brand__rule"></div>
      <div class="brand__name">Keystone Floor<br>Reviews</div>
      <div class="brand__sub">Analysis &amp; Consulting</div>
      <div class="brand__rule"></div>
    </div>
    <p class="tagline">Certified Floor Covering<br>Inspection &amp; Consulting</p>
  </section>

  <section class="card card--back" aria-label="Card back">
    <div class="card__sheen"></div>
    <div class="brand">
      <div class="brand__mark"></div>
      <div class="brand__rule"></div>
      <div class="brand__name">Keystone Floor<br>Reviews</div>
      <div class="brand__rule"></div>
    </div>
    <p class="holder">Dana Merrow</p>
    <div class="divider"></div>
    <ul class="contacts">
      <li>
        <svg viewBox="0 0 18 18" aria-hidden="true"><rect x="1" y="1" width="16" height="16" rx="3" fill="none" stroke="#fff" stroke-width="1.6"/><path d="M6 4.5l1.6 2.4-1 1c.7 1.4 1.8 2.5 3.2 3.2l1-1 2.4 1.6-1 1.8C8.6 13.6 4.6 9.6 4.2 5.6z" fill="#fff"/></svg>
        303-555-0142
      </li>
      <li>
        <svg viewBox="0 0 18 18" aria-hidden="true"><rect x="1" y="3.5" width="16" height="11" fill="#fff"/><path d="M1 3.5l8 6 8-6" fill="none" stroke="#e56f08" stroke-width="1.4"/></svg>
        dana@keystonefloorreviews.com
      </li>
      <li>
        <svg viewBox="0 0 18 18" aria-hidden="true"><circle cx="9" cy="9" r="7.5" fill="none" stroke="#fff" stroke-width="1.6"/><ellipse cx="9" cy="9" rx="3.2" ry="7.5" fill="none" stroke="#fff" stroke-width="1.2"/><path d="M1.5 9h15M3 5h12M3 13h12" stroke="#fff" stroke-width="1.2"/></svg>
        www.keystonefloorreviews.com
      </li>
    </ul>
  </section>

</main>
</body>
</html>
```